Business Card Design

We are a law firm which provides services to creditors.....we do collection litigation. I am wide open on suggestions. I was thinking of a square card? Alternatively, a vertically oriented standard card or a folded card.....something unique. I would like to use my firm logo and beyond that, I am open for any and all suggestions. I'm uncertain if the complete log is uploaded? If not, please let me email it to you.

Industry/Entity Type

Law Firm

Contact Information for Business Card

Hart, Crane & Dobbs, P.C.
Tom Dobbs, Lawyer
4387 N Larkspur Ave
Oklahoma City, OK 73924
tdobbs@HcdCounsel.com
www.HcdCounsel.com
mobile: 405-382-7914

```html
<!DOCTYPE html>
<html lang="en">
<head>
<meta charset="utf-8">
<title>Hart, Crane &amp; Dobbs, P.C. – Business Card</title>
<link href="https://fonts.googleapis.com/css2?family=Arimo:wght@400;700&display=swap" rel="stylesheet">
<style>
  :root {
    --page-bg: #e9e6e1;
    --green: #1f5a38;
    --green-deep: #0f4a2a;
    --gold: #a88a2a;
    --gold-light: #cdb35a;
    --panel: #f1f3f2;
    --ink: #1e5a3a;
  }
  html, body {
    margin: 0;
    width: 1200px;
    height: 970px;
    overflow: hidden;
    background: var(--page-bg);
    font-family: "Arimo", Arial, sans-serif;
  }
  .card {
    position: absolute;
    left: 65px;
    top: 190px;
    width: 1070px;
    height: 590px;
    box-shadow: 0 10px 30px rgba(0,0,0,0.18);
  }
  .card-frame {
    position: absolute;
    inset: 0;
  }
  .firm-name {
    position: absolute;
    left: 93px;
    top: 74px;
    margin: 0;
    font-size: 64px;
    font-weight: 700;
    color: var(--ink);
    letter-spacing: 0.5px;
    white-space: nowrap;
  }
  .person-name {
    position: absolute;
    left: 93px;
    top: 172px;
    margin: 0;
    font-size: 54px;
    font-weight: 400;
    color: var(--ink);
    white-space: nowrap;
  }
  .person-title {
    position: absolute;
    left: 95px;
    top: 232px;
    margin: 0;
    font-size: 22px;
    color: var(--ink);
  }
  .contact-list {
    position: absolute;
    left: 97px;
    top: 296px;
    margin: 0;
    padding: 0;
    list-style: none;
  }
  .contact-item {
    display: flex;
    align-items: center;
    height: 41px;
    font-size: 28px;
    color: var(--ink);
    white-space: nowrap;
  }
  .contact-icon {
    width: 30px;
    height: 30px;
    margin-right: 28px;
    flex: none;
  }
  .address {
    position: absolute;
    left: 95px;
    top: 434px;
    margin: 0;
    font-size: 26px;
    line-height: 27px;
    color: var(--ink);
    font-style: normal;
  }
  .brand-mark {
    position: absolute;
    left: 660px;
    top: 330px;
    width: 340px;
    display: flex;
    flex-direction: column;
    align-items: center;
    gap: 14px;
  }
  .brand-dot {
    width: 54px;
    height: 54px;
    border-radius: 50%;
    background: var(--green);
  }
  .brand-name {
    font-size: 30px;
    font-weight: 700;
    color: var(--green);
    white-space: nowrap;
  }
</style>
</head>
<body>
  <div class="card">
    <svg class="card-frame" width="1070" height="590" viewBox="0 0 1070 590" aria-hidden="true">
      <defs>
        <linearGradient id="gold-band" x1="0" y1="0" x2="1" y2="1">
          <stop offset="0" stop-color="#8f7420"/>
          <stop offset="0.45" stop-color="#cdb35a"/>
          <stop offset="1" stop-color="#8a6f1e"/>
        </linearGradient>
      </defs>
      <rect class="frame-gold" width="1070" height="590" fill="url(#gold-band)"/>
      <polygon class="frame-green-top-left" points="0,0 318,0 280,45 52,45 52,235 0,280" fill="var(--green)"/>
      <polygon class="frame-green-bottom-right" points="1070,355 1070,590 815,590 860,545 1017,545 1017,400" fill="var(--green-deep)"/>
      <rect class="frame-panel" x="52" y="45" width="965" height="500" fill="var(--panel)"/>
    </svg>

    <h1 class="firm-name">Hart, Crane &amp; Dobbs, P.C.</h1>
    <p class="person-name">Tom Dobbs</p>
    <p class="person-title">Lawyer</p>

    <ul class="contact-list">
      <li class="contact-item">
        <svg class="contact-icon" viewBox="0 0 30 30" aria-hidden="true">
          <rect width="30" height="30" fill="var(--green)"/>
          <rect x="10" y="7" width="10" height="16" rx="2" fill="none" stroke="#fff" stroke-width="2"/>
        </svg>
        405-382-7914
      </li>
      <li class="contact-item">
        <svg class="contact-icon" viewBox="0 0 30 30" aria-hidden="true">
          <rect width="30" height="30" fill="var(--green)"/>
          <circle cx="15" cy="15" r="8" fill="none" stroke="#fff" stroke-width="2"/>
          <line x1="7" y1="15" x2="23" y2="15" stroke="#fff" stroke-width="1.5"/>
          <ellipse cx="15" cy="15" rx="3.5" ry="8" fill="none" stroke="#fff" stroke-width="1.5"/>
        </svg>
        www.HcdCounsel.com
      </li>
      <li class="contact-item">
        <svg class="contact-icon" viewBox="0 0 30 30" aria-hidden="true">
          <rect width="30" height="30" fill="var(--green)"/>
          <rect x="7" y="9" width="16" height="12" fill="none" stroke="#fff" stroke-width="2"/>
          <polyline points="7,9 15,16 23,9" fill="none" stroke="#fff" stroke-width="2"/>
        </svg>
        tdobbs@HcdCounsel.com
      </li>
    </ul>

    <address class="address">4387 N Larkspur Ave Oklahoma City,<br>OK 73924</address>

    <div class="brand-mark">
      <div class="brand-dot"></div>
      <div class="brand-name">Hart, Crane &amp; Dobbs</div>
    </div>
  </div>
</body>
</html>
```